Design for the A4 Letterhead, envelope and A4 Folder

Design have to be clean, professional, unique (eye catchy) and high end.
Colors: Yellow (Code: 803C), Darker Grey and Black or white (optional)
Logo can be in white or black

Letterhead:
Contain: 1. Korvane Logo
2. Slogan "MADE WITH PRIDE"
3. Company information:
Korvane Valves Pte. Ltd. (Singapore)
Registration no: 201947215K
Tel: (65) 6418 2904
Fax: (65) 6472 9186
Email: sales@korvanevalves.example
Website: http://www.korvanevalves.example
4. Logo watermark

Envelope:
Contain: 1. Korvane Logo
3. website: http://www.korvanevalves.example and email address:
sales@korvanevalves.example
4. Logo watermark

Folder:
Contain: 1. Korvane Logo
3. Company's information:
Tel: (65) 6418 2904
Fax: (65) 6472 9186
4. QR Code
5. Logo watermark
6. On the inside there is a space to insert business card. Contrast colors
between the inside and cover.
Updates

For the Folder design, please be informed that we would prefer to have the Korvane logo on the left hand side of the cover page, rather than on the right hand side.And also if we could highlight the "Made with Pride" slogan with either the yellow box or black/grey box depending on the background color.For the Envelope design,it does not matter where the position of the logo is. But please also highlight the "Made with Pride" Slogan For the Letterhead design, the position of the logo must be on the left hand side and the slogan must be highlighted. In addition, please include the following company information (only for the letterhead design)Korvane Valves Pte. Ltd. (Singapore)Registration no: 200308878MTel: (65) 6535 3735Fax: (65) 6533 3570Email: sales@dynatechpumps.comWebsite: http://www.korvanevalves.example Added Wednesday, August 2, 2017

Target Market(s)

Business to Business, High End market

Industry/Entity Type

It Professional

Font styles to use
Serif

Requirements
Must have
• Design have to be clean, professional, unique (eye catchy) and high end.
Nice to have
• color contrast but still maintaining the professionalism and the seriousness
Should not have
• Messy look, futuristic look, too crowded

```html
<!DOCTYPE html>
<html lang="en">
<head>
<meta charset="utf-8">
<title>Korvane Valves – Stationery</title>
<link href="https://fonts.googleapis.com/css2?family=Source+Sans+3:wght@400;600;800&display=swap" rel="stylesheet">
<style>
  :root{
    --yellow:#ffff00;
    --grey-dark:#58585a;
    --ink:#444446;
    --paper:#f5f5f3;
    --watermark:#ebebe9;
    --bg-top:#8a8a8a;
    --bg-bottom:#4a4a4a;
  }
  *{margin:0;padding:0;box-sizing:border-box}
  html,body{width:1200px;height:754px;overflow:hidden}
  body{font-family:"Source Sans 3",sans-serif;color:var(--ink)}
  .stage{position:relative;width:1200px;height:754px;overflow:hidden;
    background:linear-gradient(to bottom,var(--bg-top),var(--bg-bottom))}
  .sheet{position:absolute;background:var(--paper);overflow:hidden;
    box-shadow:0 1px 4px rgba(0,0,0,.35)}
  .watermark{position:absolute;border-radius:50%;border:38px solid var(--watermark)}
  .accent-bar{position:absolute;background:var(--yellow)}
  .brand{position:absolute;display:flex;flex-direction:column;align-items:center}
  .brand-dot{border-radius:50%;background:var(--grey-dark)}
  .brand-name{font-weight:600;color:var(--grey-dark);letter-spacing:.5px;line-height:1}
  .slogan-band{position:absolute;height:16px;display:flex;align-items:center}
  .slogan-band .yellow{height:100%;background:var(--yellow);display:flex;align-items:center;justify-content:center;
    font-weight:800;font-size:9px;letter-spacing:.8px;color:var(--grey-dark)}
  .slogan-band .seal{width:19px;height:19px;border-radius:50%;background:var(--paper);border:2px solid var(--grey-dark);margin:0 -2px;position:relative;z-index:1}
  .slogan-band .grey{height:100%;background:var(--grey-dark);flex:1}

  /* letterhead */
  .letterhead{left:36px;top:32px;width:490px;height:690px}
  .contact{position:absolute;right:36px;top:38px;text-align:right;font-size:9px;line-height:11.3px}
  .contact .icon{display:inline-block;width:8px;margin-left:6px;color:var(--grey-dark);font-size:7px}
  .letter{position:absolute;left:37px;top:190px;width:410px}
  .greeting{font-size:13.5px;margin-bottom:25px}
  .letter p.body{font-size:7.4px;line-height:11.8px;margin-bottom:11.8px;text-align:justify}
  .closing{font-size:7.4px;margin-top:21px}
  .signature{width:80px;height:26px;margin:10px 0 0 12px;background:linear-gradient(90deg,#d9d9dc,#c9c9ce);opacity:.6}
  .signer{margin:10px 0 0 12px;font-size:9px;line-height:9px}
  .signer small{display:block;font-size:7px}

  /* envelope front */
  .envelope-front{left:546px;top:209px;width:548px;height:248px}
  .flap{position:absolute;left:0;top:0}
  /* envelope back */
  .envelope-back{left:547px;top:471px;width:550px;height:249px}
  .return-address{position:absolute;left:23px;top:87px;font-size:8px;line-height:11.5px}
</style>
</head>
<body>
<div class="stage">

  <!-- Letterhead -->
  <section class="sheet letterhead">
    <div class="watermark" style="left:180px;top:395px;width:440px;height:440px"></div>
    <div class="accent-bar" style="left:1px;top:21px;width:6px;height:76px"></div>
    <div class="brand" style="left:50px;top:22px">
      <div class="brand-dot" style="width:40px;height:40px;margin-bottom:8px"></div>
      <div class="brand-name" style="font-size:18px">KORVANE</div>
    </div>
    <div class="contact">
      <div>Korvane Valves Pte. Ltd. (Singapore)</div>
      <div>(65) 6418 2904<span class="icon">&#9990;</span></div>
      <div>(65) 6472 9186<span class="icon">&#9113;</span></div>
      <div>sales@korvanevalves.example<span class="icon">&#9993;</span></div>
    </div>
    <div class="letter">
      <p class="greeting">Dear Mr. Hale,</p>
      <p class="body">Lorem ipsum dolor sit amet, consectetur adipiscing elit. Donec orci purus, luctus vitae dignissim eu, iaculis sed purus. Vivamus faucibus, ipsum nec aliquet viverra, leo mauris condimentum ligula, sit amet sagittis enim ligula quis arcu. Nam egestas tortor id nisi porttitor mattis. In tortor ante, ultricies in suscipit a, tempus non massa. Vivamus et auctor mi. Fusce vel massa nulla. Phasellus nec eros mauris, et scelerisque orci.</p>
      <p class="body">Donec malesuada orci vitae nulla accumsan porta a id massa. Quisque accumsan iaculis magna sit amet fringilla. Maecenas consequat, magna eget tincidunt semper, odio nibh rutrum mi, id feugiat ante nisi eu risus. Vestibulum nunc orci, rhoncus a placerat in, ultricies in mi. Cras mattis varius eros, vel fringilla nisi suscipit eget. Quisque scelerisque sagittis nulla at porttitor.</p>
      <p class="body">Sed id augue vitae urna euismod commodo aliquet a quam. Pellentesque arcu velit, cursus et malesuada ut, consequat et diam. Nullam erat sem, rhoncus id ullamcorper vitae, rhoncus et arcu. In ultricies ultricies nulla, ut rutrum nisi iaculis at. Donec eu magna a metus ornare faucibus. Fusce aliquet faucibus ultricies. Morbi semper, est id tincidunt gravida, sem arcu adipiscing lacus, ac bibendum nulla leo eu purus. Quisque nec diam sed risus consectetur a ccumsan quis quis nibh. Vestibulum id purus lorem.</p>
      <p class="body">It is a long established fact that a reader will be distracted by the readable content of a page when looking at its layout. The point of using Lorem Ipsum is that it has a more-or-less normal distribution of letters, as opposed to using 'Content here, content here', making it look like readable English. Many desktop publishing packages</p>
      <p class="closing">Sincerely,</p>
      <div class="signature" role="img" aria-label="Handwritten signature"></div>
      <div class="signer">DANIEL HALE<small>CEO/ Founder</small></div>
    </div>
    <div class="slogan-band" style="left:0;top:662px;width:490px">
      <div class="yellow" style="width:360px">MADE WITH PRIDE</div>
      <div class="seal"></div>
      <div class="grey"></div>
    </div>
  </section>

  <!-- Envelope front -->
  <section class="sheet envelope-front">
    <svg class="flap" width="548" height="92" viewBox="0 0 548 92" aria-hidden="true">
      <path d="M0 0 H548 L534 62 Q527 91 497 91 H51 Q21 91 14 62 Z" fill="var(--yellow)"/>
    </svg>
    <div class="brand" style="left:245px;top:22px">
      <div class="brand-dot" style="width:33px;height:33px;margin-bottom:6px"></div>
      <div class="brand-name" style="font-size:15px">KORVANE</div>
    </div>
    <div class="slogan-band" style="left:0;top:211px;width:548px">
      <div class="yellow" style="width:420px">MADE WITH PRIDE</div>
      <div class="seal"></div>
      <div class="grey"></div>
    </div>
  </section>

  <!-- Envelope back -->
  <section class="sheet envelope-back">
    <div class="watermark" style="left:360px;top:62px;width:290px;height:290px"></div>
    <div class="accent-bar" style="left:0;top:19px;width:6px;height:64px"></div>
    <div class="brand" style="left:24px;top:21px">
      <div class="brand-dot" style="width:38px;height:38px;margin-bottom:7px"></div>
      <div class="brand-name" style="font-size:15px">KORVANE</div>
    </div>
    <div class="return-address">
      <div>Korvane Valves Pte. Ltd. (Singapore)</div>
      <div>&#9990; (65) 6418 2904</div>
      <div>&#9113; (65) 6472 9186</div>
    </div>
  </section>

</div>
</body>
</html>
```